High-end law practice specializing in closely held business succession planning and complex estates

Solo practitioner whose practice specializes in high-net worth, complex estate planning needs muliple versions of letterhead black and white, please. Letterhead should incorporate slogan, "Protecting your family business is my business," for one and "Complex Estate Planning"; third with no slogan. All for The Law Office of Marcy Lynn Pettibone, PC, 418 Cedar Hollow Ln., Newport News, Virginia 23648, Tel. 757-555-0142 Fax tbd email: marcy@mlplawgroup.example; Marcy Lynn Pettibone, Esq., principal, licensed in VA, NY, DC
Updates

Project Deadline Extended
Reason: My internet service went down and I can only view designs on my smart phone -- it's just too hard to review. So sorry! Working with my ISP now. Please be patient!

Target Market(s)

High net worth clients with complex estate planning needs, family businesses, family farmers, family foresters -- people with unique estate/succession planning needs who need a specialist who understands them.

Industry/Entity Type

Business

Font styles to use
Script

Requirements
Must have
• A high-end look and feel, connoting trustworthiness, special knowledge, and expertise.

```html
<!DOCTYPE html>
<html lang="en">
<head>
<meta charset="utf-8">
<title>Marcy Lynn Pettibone, Esq. — Letterhead</title>
<link href="https://fonts.googleapis.com/css2?family=Roboto:wght@300;400;700&display=swap" rel="stylesheet">
<style>
  :root {
    --paper: #fdfdfd;
    --ink-strong: #3a3a3a;
    --ink: #4a4a4a;
    --ink-soft: #606060;
    --band: #6d6e70;
    --band-line: #f2f2f2;
    --rule: #6a6a6a;
  }
  html, body {
    margin: 0;
    padding: 0;
    overflow: hidden;
    background: var(--paper);
  }
  .letterhead {
    position: relative;
    width: 849px;
    height: 1200px;
    background: var(--paper);
    font-family: "Roboto", Arial, sans-serif;
    color: var(--ink);
    overflow: hidden;
  }
  .sender {
    position: absolute;
    left: 43px;
    top: 40px;
  }
  .sender-name {
    margin: 0;
    font-size: 28px;
    font-weight: 700;
    color: var(--ink-strong);
    line-height: 1.1;
    letter-spacing: -0.2px;
  }
  .sender-title {
    margin: 4px 0 0;
    font-size: 19px;
    font-weight: 400;
    line-height: 1.3;
    color: var(--ink);
  }
  .practice-band {
    position: absolute;
    left: 385px;
    top: 57px;
    width: 460px;
    height: 65px;
    background: var(--band);
  }
  .practice-band svg { display: block; }
  .practice-band .icon * {
    fill: none;
    stroke: var(--band-line);
    stroke-width: 1.4;
    stroke-linecap: round;
    stroke-linejoin: round;
  }
  .slogan {
    position: absolute;
    left: 385px;
    top: 125px;
    margin: 0;
    font-size: 20.3px;
    font-weight: 300;
    color: var(--ink-soft);
    letter-spacing: -0.1px;
  }
  .contact {
    position: absolute;
    left: 46px;
    top: 956px;
    margin: 0;
    padding: 0;
    list-style: none;
    font-size: 16.5px;
    font-weight: 400;
    color: var(--ink-soft);
  }
  .contact-item {
    display: flex;
    align-items: flex-start;
    margin-bottom: 11px;
    line-height: 20px;
  }
  .contact-item.address { margin-bottom: 6px; }
  .contact-icon {
    flex: 0 0 18px;
    width: 18px;
    height: 18px;
    margin-right: 7px;
    margin-top: 1px;
  }
  .contact-icon * {
    fill: none;
    stroke: var(--ink-soft);
    stroke-width: 1.1;
  }
  .footer-rule {
    position: absolute;
    left: 313px;
    top: 943px;
    width: 2px;
    height: 252px;
    background: var(--rule);
  }
</style>
</head>
<body>
<main class="letterhead">
  <header class="sender">
    <h1 class="sender-name">Marcy Lynn Pettibone</h1>
    <p class="sender-title">Esq., principal,<br>licensed in VA, NY, DC</p>
  </header>

  <div class="practice-band" role="img" aria-label="Row of practice-area icons: law book, column, gavel, scales, calculator, sealed document, passport and signed agreement">
    <svg width="460" height="65" viewBox="0 0 460 65" aria-hidden="true">
      <!-- law book -->
      <g class="icon">
        <rect x="23" y="15" width="26" height="34" rx="2"/>
        <line x1="28" y1="15" x2="28" y2="49"/>
        <line x1="33" y1="24" x2="44" y2="24"/>
        <line x1="33" y1="29" x2="44" y2="29"/>
      </g>
      <!-- column -->
      <g class="icon">
        <path d="M66 22h28l-14-7z"/>
        <line x1="70" y1="25" x2="70" y2="44"/>
        <line x1="77" y1="25" x2="77" y2="44"/>
        <line x1="83" y1="25" x2="83" y2="44"/>
        <line x1="90" y1="25" x2="90" y2="44"/>
        <rect x="64" y="45" width="32" height="4"/>
      </g>
      <!-- gavel -->
      <g class="icon">
        <rect x="118" y="17" width="20" height="10" rx="2" transform="rotate(-40 128 22)"/>
        <line x1="131" y1="26" x2="146" y2="41"/>
        <rect x="114" y="42" width="22" height="4"/>
        <line x1="111" y1="49" x2="139" y2="49"/>
      </g>
      <!-- scales -->
      <g class="icon">
        <line x1="187" y1="14" x2="187" y2="47"/>
        <line x1="171" y1="21" x2="203" y2="21"/>
        <path d="M171 21l-6 13h12z"/>
        <path d="M203 21l-6 13h12z"/>
        <path d="M165 34a6 4 0 0 0 12 0M197 34a6 4 0 0 0 12 0"/>
        <line x1="178" y1="49" x2="196" y2="49"/>
      </g>
      <!-- calculator -->
      <g class="icon">
        <rect x="229" y="14" width="24" height="35" rx="2"/>
        <rect x="233" y="18" width="16" height="7"/>
        <path d="M234 30h3M240 30h3M246 30h3M234 36h3M240 36h3M246 36h3M234 42h3M240 42h3M246 42h3"/>
      </g>
      <!-- sealed document -->
      <g class="icon">
        <rect x="277" y="14" width="24" height="31" rx="1"/>
        <line x1="282" y1="21" x2="296" y2="21"/>
        <line x1="282" y1="27" x2="296" y2="27"/>
        <line x1="282" y1="33" x2="290" y2="33"/>
        <circle cx="299" cy="42" r="6"/>
      </g>
      <!-- passport -->
      <g class="icon">
        <rect x="343" y="14" width="24" height="35" rx="2"/>
        <circle cx="355" cy="27" r="6"/>
        <line x1="349" y1="27" x2="361" y2="27"/>
        <line x1="355" y1="21" x2="355" y2="33"/>
        <line x1="349" y1="41" x2="361" y2="41"/>
      </g>
      <!-- signed agreement -->
      <g class="icon">
        <rect x="401" y="14" width="24" height="35" rx="1"/>
        <line x1="406" y1="21" x2="420" y2="21"/>
        <line x1="406" y1="27" x2="420" y2="27"/>
        <path d="M406 40l4 4 8-9"/>
        <path d="M427 30l10-10 3 3-10 10-4 1z"/>
      </g>
    </svg>
  </div>
  <p class="slogan">Protecting your family business is my business.</p>

  <ul class="contact">
    <li class="contact-item address">
      <svg class="contact-icon" viewBox="0 0 18 18" aria-hidden="true">
        <path d="M9 16.5c-3-3.6-5-6.4-5-9a5 5 0 0 1 10 0c0 2.6-2 5.4-5 9z"/>
        <circle cx="9" cy="7.4" r="1.9"/>
      </svg>
      <span>PC, 418 Cedar Hollow Ln.,<br>Newport News, Virginia 23648,</span>
    </li>
    <li class="contact-item phone">
      <svg class="contact-icon" viewBox="0 0 18 18" aria-hidden="true">
        <path d="M2 7c0-2 3-3.5 7-3.5S16 5 16 7l-3 1-1-2H6L5 8z"/>
        <rect x="4.5" y="9" width="9" height="5.5" rx="1"/>
        <circle cx="9" cy="11.7" r="1.4"/>
      </svg>
      <span>757-555-0142</span>
    </li>
    <li class="contact-item fax">
      <svg class="contact-icon" viewBox="0 0 18 18" aria-hidden="true">
        <rect x="5" y="2" width="8" height="5"/>
        <rect x="2" y="7" width="14" height="6" rx="1"/>
        <rect x="5" y="11" width="8" height="5"/>
        <line x1="6.5" y1="13.5" x2="11.5" y2="13.5"/>
      </svg>
      <span>757-555-0198</span>
    </li>
    <li class="contact-item mobile">
      <svg class="contact-icon" viewBox="0 0 18 18" aria-hidden="true">
        <rect x="4.5" y="1.5" width="9" height="15" rx="1.2"/>
        <line x1="4.5" y1="13" x2="13.5" y2="13"/>
        <line x1="8" y1="14.8" x2="10" y2="14.8"/>
      </svg>
      <span>757-555-0176</span>
    </li>
    <li class="contact-item email">
      <svg class="contact-icon" viewBox="0 0 18 18" aria-hidden="true">
        <rect x="2" y="4.5" width="14" height="9"/>
        <path d="M2 4.5l7 5 7-5M2 13.5l5-4.5M16 13.5l-5-4.5"/>
      </svg>
      <span>marcy@mlplawgroup.example</span>
    </li>
    <li class="contact-item web">
      <svg class="contact-icon" viewBox="0 0 18 18" aria-hidden="true">
        <circle cx="9" cy="9" r="6.5"/>
        <ellipse cx="9" cy="9" rx="2.8" ry="6.5"/>
        <line x1="2.5" y1="9" x2="15.5" y2="9"/>
        <path d="M3.5 5.8h11M3.5 12.2h11"/>
      </svg>
      <span>www.mlplawgroup.example</span>
    </li>
  </ul>
  <div class="footer-rule" aria-hidden="true"></div>
</main>
</body>
</html>
```